Need Business Card for our Real Estate Business with Sales Executive's Picture

PANTONE 484 C ( RED)

PANTONE 2766 C ( BLUE

Industry/Entity Type

Real Estate

Contact Information for Business Card

Name, Mobile, email, & picture of Person
Agency Phone, address, Web address

Requirements
Must have
• Our Logo Colours, Agent Picture,

```html
<!DOCTYPE html>
<html lang="en">
<head>
<meta charset="utf-8">
<title>Meridian Real Estate – Business Card</title>
<link href="https://fonts.googleapis.com/css2?family=Crimson+Text:wght@400;600&display=swap" rel="stylesheet">
<style>
  :root {
    --navy: #0f1f5c;
    --navy-deep: #0a1548;
    --red: #9c1224;
    --white: #ffffff;
    --paper: #f3f3f1;
    --backdrop: #e6e4df;
    --suit: #2f55b8;
    --suit-dark: #16296e;
  }
  * { margin: 0; padding: 0; box-sizing: border-box; }
  html, body { width: 1200px; height: 780px; overflow: hidden; background: var(--backdrop); }
  .canvas {
    width: 1200px; height: 780px;
    display: flex; align-items: center; justify-content: center; gap: 40px;
  }
  .card {
    width: 540px; height: 309px; position: relative; overflow: hidden;
    box-shadow: 0 8px 24px rgba(0,0,0,.18);
    font-family: "Crimson Text", serif;
  }

  /* Front */
  .card-front { background: var(--navy); }
  .front-header {
    position: absolute; left: 0; top: 0; width: 100%; height: 112px;
    background: var(--paper);
  }
  .front-logo { position: absolute; left: 30px; top: 22px; }
  .wordmark {
    font-weight: 400; color: var(--navy);
    font-size: 46px; letter-spacing: 3px; line-height: 1;
  }
  .logo-rule { width: 250px; height: 1px; background: var(--navy); margin-top: 6px; }
  .tagline {
    font-size: 10px; letter-spacing: 2.5px; text-transform: uppercase;
    color: var(--navy); margin-top: 4px; padding-left: 120px;
  }
  .name-band {
    position: absolute; left: 0; top: 112px; width: 100%; height: 42px;
    background: var(--red); border-bottom: 3px solid var(--white);
    display: flex; align-items: center; padding-left: 30px;
    color: var(--white);
  }
  .agent-name { font-size: 19px; letter-spacing: 1px; text-transform: uppercase; }
  .agent-divider { width: 1px; height: 18px; background: var(--white); margin: 0 10px; }
  .agent-role { font-size: 16px; }
  .contact-list {
    position: absolute; left: 30px; top: 168px; list-style: none;
    color: var(--white); font-size: 15px; line-height: 1.22;
  }
  .contact-list li { display: flex; align-items: center; gap: 6px; }
  .contact-icon { width: 14px; height: 14px; flex: none; }
  .agent-photo {
    position: absolute; right: 0; top: 0; width: 220px; height: 309px;
    background:
      linear-gradient(180deg, var(--paper) 0%, var(--paper) 22%, var(--suit) 48%, var(--suit-dark) 100%);
  }

  /* Back */
  .card-back { background: radial-gradient(ellipse at 60% 40%, #172b78 0%, var(--navy-deep) 80%); }
  .back-logo { position: absolute; left: 0; right: 0; top: 80px; text-align: center; }
  .back-logo .wordmark { color: var(--white); font-size: 56px; }
  .back-logo .logo-rule { width: 290px; background: var(--white); margin: 8px auto 0; }
  .back-logo .tagline { color: var(--white); padding-left: 0; font-size: 11px; margin-top: 6px; }
  .web-band {
    position: absolute; left: 0; bottom: 26px; width: 100%; height: 34px;
    background: var(--red);
    border-top: 3px solid var(--white); border-bottom: 3px solid var(--white);
    box-shadow: 0 -5px 0 var(--navy-deep), 0 -7px 0 var(--white);
    display: flex; align-items: center; padding-left: 30px;
    color: var(--white); font-size: 14px; letter-spacing: 3px;
  }
</style>
</head>
<body>
<main class="canvas">
  <section class="card card-front">
    <header class="front-header">
      <div class="front-logo">
        <div class="wordmark">MERIDIAN</div>
        <div class="logo-rule"></div>
        <div class="tagline">Real Estate</div>
      </div>
    </header>
    <div class="name-band">
      <span class="agent-name">Owen Carter</span>
      <span class="agent-divider"></span>
      <span class="agent-role">Owner</span>
    </div>
    <ul class="contact-list">
      <li>PO BOX 456 Harbour Lane</li>
      <li>3rd street Brisbane</li>
      <li><svg class="contact-icon" viewBox="0 0 14 14"><circle cx="7" cy="7" r="6.2" fill="none" stroke="#fff"/><path d="M4.5 4h1.6l.6 1.8-.9.7a5 5 0 0 0 1.9 1.9l.7-.9 1.8.6v1.6c-3.2.3-6-2.5-5.7-5.7z" fill="#fff"/></svg>(555) 014-2287</li>
      <li><svg class="contact-icon" viewBox="0 0 14 14"><circle cx="7" cy="7" r="6.2" fill="none" stroke="#fff"/><rect x="3.8" y="4.8" width="6.4" height="4.4" fill="none" stroke="#fff" stroke-width=".9"/><path d="M3.8 4.8 7 7.4l3.2-2.6" fill="none" stroke="#fff" stroke-width=".9"/></svg>hello@meridianhomes.com</li>
      <li><svg class="contact-icon" viewBox="0 0 14 14"><circle cx="7" cy="7" r="6.2" fill="none" stroke="#fff"/><circle cx="7" cy="7" r="3.4" fill="none" stroke="#fff" stroke-width=".9"/><path d="M3.6 7h6.8M7 3.6v6.8" stroke="#fff" stroke-width=".8"/></svg>www.meridianhomes.com</li>
    </ul>
    <div class="agent-photo" role="img" aria-label="Photo of the sales executive in a blue suit and tie, smiling, set against the white top of the card"></div>
  </section>

  <section class="card card-back">
    <div class="back-logo">
      <div class="wordmark">MERIDIAN</div>
      <div class="logo-rule"></div>
      <div class="tagline">Real Estate</div>
    </div>
    <div class="web-band">www.MERIDIANHOMES.com</div>
  </section>
</main>
</body>
</html>
```